AUTOMOTIVE/ CAR REPAIRS / CRASH REPAIRS / PAINT SPRAYING AND PANEL BEATING

AUTOMOTIVE REPAIR. CAR / MOTORCYCLES GOT LOGO DESIGN / DID THINK ABOUT FACEBOOK DONT NOALREADY HAVE WEB ADRESS www.brenvashine.co.uk and mail sales@brenvashine,co.uk NEED SOMETHINK I CAN MANAGE TO UPLOAD PICTURES IN TO A GALLERY OR SOMETHINGLIKE THAT I ALSO SELL CAR AND MOTORCYCLES MAYBE A SELLS PAGE WITH A TILLWAVE LINK

Target Market(s)

TRADE / GENERAL PUBLIC

Industry/Entity Type

Automotive

Coding

Coded - Design and coding required

Number of Pages Required

4 page

Font styles to use
Serif
Sans Serif

Colors

Designer to choose colors to be used in the design.

Requirements
Must have
• GALLERY/ SHOP TO SALE CARS AND MOTORCYCLE / LOGOS OF MATERIALS I USE DORFLINT / KEBO / VASTINCO / Q WRAP / GLENBRUSH
• CONTACT US
Nice to have
• TILLWAVE / EASY TO MANAGE / VIDEO CLIP OF DORFLINT HUE PLANNER Z7
• SWIFT BLEND PAINT TONVIEW WETLINE AND TULVOKE

```html
<!DOCTYPE html>
<html lang="en">
<head>
<meta charset="utf-8">
<title>Brenvashine Bodyshop</title>
<link href="https://fonts.googleapis.com/css2?family=Montserrat:wght@400;500;600;700&display=swap" rel="stylesheet">
<style>
:root{
  --red:#e3111b;
  --navy:#1c2231;
  --navy-dark:#141821;
  --ink:#0d0f14;
  --grey-dark:#1a1d23;
  --text:#ffffff;
  --muted:#c9ccd3;
  --logo-grey:#5b5f66;
}
*{margin:0;padding:0;box-sizing:border-box}
html,body{width:1200px;height:4882px;overflow:hidden}
body{font-family:"Montserrat",sans-serif;color:var(--text);background:var(--navy-dark);position:relative}
section,header,footer{position:absolute;left:0;width:1200px}
.red{color:var(--red)}
.heading{font-size:34px;font-weight:500;text-align:center;letter-spacing:.5px}
.heading b{font-weight:700;color:var(--red)}

/* header */
.site-header{top:0;height:98px;background:var(--red)}
.site-header .topbar{position:absolute;left:420px;top:0;right:0;height:47px;background:var(--ink)}
.brand-panel{position:absolute;left:62px;top:0;width:390px;height:98px;background:var(--ink);clip-path:polygon(18px 0,100% 0,calc(100% - 18px) 100%,0 100%)}
.brand{position:absolute;left:95px;top:18px;width:300px;text-align:center}
.brand .name{font-size:34px;font-weight:700;letter-spacing:2px;line-height:1}
.brand .sub{font-size:12px;letter-spacing:9px;margin-top:6px}
.contact-line{position:absolute;top:12px;font-size:18px;letter-spacing:1px;display:flex;align-items:center;gap:12px}
.contact-line svg{width:16px;height:16px;fill:#fff}
.nav{position:absolute;top:60px;left:475px;display:flex;gap:0;font-size:15px;font-weight:500}
.nav a{color:#fff;text-decoration:none;width:113px}
.nav a.active{text-decoration:underline}

/* hero */
.hero{top:98px;height:515px;background:linear-gradient(100deg,#6f6a68 0%,#a39a92 35%,#7d3b35 60%,#3a2f2d 100%)}
.hero .photo{position:absolute;inset:0}
.hero-brand{position:absolute;left:88px;top:166px;width:370px}
.hero-brand .name{font-size:56px;font-weight:500;letter-spacing:2px;line-height:1}
.hero-brand .sub{font-size:18px;letter-spacing:16px;text-align:center;margin-top:14px;font-weight:500;color:#111}
.btn{display:inline-flex;align-items:center;gap:8px;background:var(--red);color:#fff;border-radius:26px;font-weight:600;font-size:18px;text-transform:uppercase;padding:11px 22px}
.btn svg{width:16px;height:16px}
.hero .btn{position:absolute;left:182px;top:298px}
.dots{position:absolute;left:551px;top:465px;display:flex;gap:11px}
.dots span{width:15px;height:15px;border-radius:50%;border:2px solid #fff;background:#222}
.dots span.on{background:var(--red)}

/* appointment */
.appointment{top:613px;height:387px;background:var(--navy);text-align:center}
.appointment h2{font-size:34px;font-weight:500;margin-top:92px}
.appointment .addr{font-size:15px;margin-top:14px}
.fields{display:flex;gap:16px;justify-content:center;margin-top:36px}
.field{width:288px;height:48px;border:1.5px solid #c9ccd3;display:flex;align-items:center;justify-content:space-between;padding:0 18px;font-size:15px}
.field svg{width:15px;height:15px;fill:#fff}
.appointment .note{font-size:14px;font-style:italic;font-weight:500;margin-top:30px}

/* about */
.about{top:1000px;height:511px;background:var(--navy-dark)}
.about h2{position:absolute;left:88px;top:92px;font-size:36px;font-weight:500;line-height:1.15}
.about h2 b{color:var(--red);font-weight:700}
.about p{position:absolute;left:88px;width:470px;font-size:16px;line-height:1.65}
.about .p1{top:186px}
.about .p2{top:250px;font-weight:500}
.about .btn{position:absolute;left:88px;top:358px;font-size:17px}
.about-media{position:absolute;left:592px;top:98px;width:520px;height:312px}
.about-media .img{position:absolute;inset:0;background:linear-gradient(135deg,#b7b7b7,#8d8d8d);clip-path:polygon(0 0,100% 0,100% 100%,0 100%)}
.about-media .tl{position:absolute;left:0;top:0;width:28px;height:120px;background:var(--red);clip-path:polygon(0 0,100% 0,0 100%)}
.about-media .br{position:absolute;right:0;bottom:0;width:28px;height:200px;background:var(--red);clip-path:polygon(100% 0,100% 100%,0 100%)}

.divider-mark{position:absolute;left:575px;width:50px;height:50px;border-radius:50%;background:#fff;z-index:2}

/* services */
.services{top:1511px;height:926px;background:var(--navy)}
.services .heading{margin-top:85px}
.card{position:absolute;width:447px;height:313px;overflow:hidden}
.card .img{position:absolute;inset:0}
.card .tl{position:absolute;left:0;top:0;width:26px;height:140px;background:var(--red);clip-path:polygon(0 0,100% 0,0 100%)}
.card .br{position:absolute;right:0;bottom:0;width:26px;height:210px;background:var(--red);clip-path:polygon(100% 0,100% 100%,0 100%)}
.card h3{position:absolute;left:0;right:0;bottom:18px;text-align:center;font-size:22px;font-weight:600;text-shadow:0 1px 3px rgba(0,0,0,.6)}

/* why us */
.why{top:2437px;height:863px;background:var(--grey-dark);text-align:center}
.why .heading{margin-top:92px}
.why p{width:980px;margin:18px auto 0;font-size:15px;line-height:1.75}
.feature{position:absolute;width:180px;text-align:center;font-size:16px;line-height:1.3}
.feature .ring{width:80px;height:80px;border-radius:50%;border:2px solid #fff;margin:0 auto 8px;display:flex;align-items:center;justify-content:center;background:#141821}
.feature .ring.on{background:var(--red)}
.feature svg{width:40px;height:40px;stroke:#fff;fill:none;stroke-width:2}
.why .cars{position:absolute;left:142px;top:420px;width:835px;height:360px;background:radial-gradient(ellipse at 40% 50%,#c8262b 0%,#9e2a2a 35%,#6d7d8c 65%,rgba(26,29,35,0) 75%)}

/* gallery */
.gallery{top:3300px;height:492px;background:var(--navy)}
.gallery .heading{margin-top:90px}
.gallery .thumb{position:absolute;top:155px;width:286px;height:262px}
.arrow{position:absolute;top:270px;width:20px;height:28px}
.arrow svg{width:20px;height:28px;stroke:#fff;stroke-width:3;fill:none}

/* partners */
.partners{top:3792px;height:248px;background:var(--navy);display:flex;align-items:center;justify-content:space-around;padding:0 80px}
.partners span{color:var(--logo-grey);font-size:30px;font-weight:700;letter-spacing:1px}

/* contact */
.contact{top:4040px;height:526px;background:var(--ink)}
.map{position:absolute;left:0;top:0;width:600px;height:526px;background:linear-gradient(135deg,#f0efec,#e4e2dd 70%,#c8e6b4)}
.contact-panel{position:absolute;left:600px;top:0;width:600px;height:526px;background:linear-gradient(160deg,#1b1e24,#0e1014)}
.contact-panel h2{position:absolute;left:43px;top:28px;font-size:34px;font-weight:500}
.contact-panel h2 b{color:var(--red);font-weight:700}
.input{position:absolute;height:42px;border:1.5px solid #c9ccd3;font-size:14px;padding:10px 12px}
.contact-panel .btn{position:absolute;left:44px;top:344px;padding:11px 48px;font-size:17px}
.info{position:absolute;font-size:15px;line-height:1.45;display:flex;gap:10px}
.info svg{width:16px;height:16px;fill:#fff;flex:none;margin-top:2px}

/* footer */
.site-footer{top:4566px;height:316px;background:var(--navy-dark);text-align:center}
.site-footer .brand-f{margin-top:58px}
.site-footer .brand-f .name{font-size:34px;font-weight:700;letter-spacing:2px}
.site-footer .brand-f .sub{font-size:12px;letter-spacing:9px;margin-top:4px}
.foot-nav{margin-top:34px;font-size:15px}
.foot-nav span{margin:0 10px}
.foot-services{margin-top:18px;font-size:14px}
.foot-services span{margin:0 6px}
.pay{margin-top:22px;font-size:20px;font-weight:700;color:#2a6fd6}
.copy{margin-top:20px;font-size:13px}
.code-tag{position:absolute;right:30px;bottom:18px;font-size:12px}
</style>
</head>
<body>

<header class="site-header">
  <div class="topbar"></div>
  <div class="brand-panel"></div>
  <div class="brand"><div class="name">BRENVASHINE</div><div class="sub">BODYSHOP</div></div>
  <div class="contact-line" style="left:474px">
    <svg viewBox="0 0 24 24"><path d="M6.6 10.8a15 15 0 0 0 6.6 6.6l2.2-2.2c.3-.3.7-.4 1-.2 1.1.4 2.3.6 3.6.6.6 0 1 .4 1 1V20c0 .6-.4 1-1 1A17 17 0 0 1 3 4c0-.6.4-1 1-1h3.5c.6 0 1 .4 1 1 0 1.3.2 2.5.6 3.6.1.3 0 .7-.2 1z"/></svg>07700 900418
  </div>
  <div class="contact-line" style="left:738px">
    <svg viewBox="0 0 24 24"><path d="M2 5h20v14H2z M2 5l10 8 10-8" /></svg>sales@brenvashine.co.uk
  </div>
  <nav class="nav">
    <a class="active">HOME</a><a>ABOUT US</a><a>SERVICE</a><a>CUSTOM</a><a>GALLERY</a><a>CONTACT</a>
  </nav>
</header>

<section class="hero">
  <div class="photo" role="img" aria-label="Red sports saloon driving fast on an open road at sunset"></div>
  <div class="hero-brand"><div class="name">BRENVASHINE</div><div class="sub">BODYSHOP</div></div>
  <span class="btn">Shop now <svg viewBox="0 0 16 16"><circle cx="8" cy="8" r="8" fill="#fff"/><path d="M6 4l4 4-4 4" stroke="#e3111b" stroke-width="2" fill="none"/></svg></span>
  <div class="dots"><span></span><span></span><span></span><span class="on"></span></div>
</section>

<section class="appointment">
  <h2>APPOINTMENT</h2>
  <div class="addr">Brenvashine Bodyshop &nbsp;Fernlow Business Park Kiln Lane Ashcombe Derbyshire DE99 2QX</div>
  <div class="fields">
    <div class="field">Date <svg viewBox="0 0 16 16"><rect x="1" y="3" width="14" height="12"/></svg></div>
    <div class="field">Time <svg viewBox="0 0 16 16"><circle cx="8" cy="8" r="7"/></svg></div>
    <div class="field">Price <svg viewBox="0 0 16 16"><path d="M3 6h10l-5 5z"/></svg></div>
  </div>
  <div class="note">If You Are Unable To Keep Your Appointment, Please Contact Us As Soon As Possible</div>
</section>

<section class="about">
  <h2><b>BRENVASHINE</b> YOUR ONE<br><b>STOP BODYSHOP</b></h2>
  <p class="p1">Fully qualified trained technicians family run business established over 30 years</p>
  <p class="p2">Brenvashine, based in Ashcombe, Derbyshire established in August, 1985 has grown to become Derbyshire's premiere manufacturer approved accident repair centre.</p>
  <span class="btn">Read more <svg viewBox="0 0 16 16"><circle cx="8" cy="8" r="8" fill="#fff"/><path d="M6 4l4 4-4 4" stroke="#e3111b" stroke-width="2" fill="none"/></svg></span>
  <div class="about-media">
    <div class="img" role="img" aria-label="Row of restored classic and modern cars in assorted colours"></div>
    <div class="tl"></div><div class="br"></div>
  </div>
</section>
<div class="divider-mark" style="top:1487px"></div>

<section class="services">
  <h2 class="heading">WE <b>PROVIDE</b></h2>
  <div class="card" style="left:127px;top:159px"><div class="img" role="img" aria-label="Stripped car body shell in primer" style="background:linear-gradient(135deg,#8c8a86,#5a5855)"></div><div class="tl"></div><div class="br"></div><h3>Car Body Repairs</h3></div>
  <div class="card" style="left:626px;top:159px"><div class="img" role="img" aria-label="Painter in protective suit spraying a motorcycle part" style="background:linear-gradient(135deg,#d9d9d9,#8e8e90)"></div><div class="tl"></div><div class="br"></div><h3>Motorcycle Painting</h3></div>
  <div class="card" style="left:127px;top:520px"><div class="img" role="img" aria-label="Close-up of a painted alloy wheel" style="background:radial-gradient(circle at 40% 50%,#9a9a9a,#3a3a3a)"></div><div class="tl"></div><div class="br"></div><h3>Wheel Painting</h3></div>
  <div class="card" style="left:626px;top:520px"><div class="img" role="img" aria-label="Blue car masked up for paintwork" style="background:linear-gradient(135deg,#2c3d6a,#4b5366 60%,#bdb48a)"></div><div class="tl"></div><div class="br"></div><h3>IE Cars and Bikes</h3></div>
</section>

<section class="why">
  <h2 class="heading">WHY <b>US</b></h2>
  <p>As a small company we are able to offer an exceptionally personal service. Whenever you call us we aim for you to be able to speak directly to the person performing your car body repairs, who will give you plain speaking, objective advice. This, combined with our many years' experience and competitive prices makes us the perfect choice for those in need of any car body repair.</p>
  <div class="cars" role="img" aria-label="Group of classic sports cars mid restoration, red and silver bodies"></div>
  <div class="feature" style="left:117px;top:280px"><div class="ring"><svg viewBox="0 0 40 40"><path d="M10 10l14 14M22 12l6-6 6 6-6 6z"/></svg></div>Full or part<br>resprays</div>
  <div class="feature" style="left:312px;top:248px"><div class="ring"><svg viewBox="0 0 40 40"><path d="M10 26h20M14 26V14h12v12M18 14V8h4v6"/></svg></div>Dent &amp; scratch<br>removal</div>
  <div class="feature" style="left:502px;top:288px"><div class="ring on"><svg viewBox="0 0 40 40"><path d="M8 24h24v6H8zM12 24l3-8h10l3 8M12 12h16"/></svg></div>Bumper repair</div>
  <div class="feature" style="left:696px;top:333px"><div class="ring"><svg viewBox="0 0 40 40"><path d="M8 26h24v-6l-5-6H14l-6 6z"/><circle cx="14" cy="27" r="3"/><circle cx="26" cy="27" r="3"/></svg></div>Accident repair</div>
  <div class="feature" style="left:888px;top:348px"><div class="ring"><svg viewBox="0 0 40 40"><circle cx="20" cy="20" r="10"/><circle cx="20" cy="20" r="3"/></svg></div>Alloy wheel's<br>refurbished, repaired<br>&amp; painted</div>
</section>
<div class="divider-mark" style="top:3276px"></div>

<section class="gallery">
  <h2 class="heading">OUR <b>GALLERY</b></h2>
  <div class="arrow" style="left:74px"><svg viewBox="0 0 20 28"><path d="M15 3L5 14l10 11"/></svg></div>
  <div class="thumb" style="left:152px" role="img" aria-label="Front of a silver saloon car in the workshop" style=""><div style="width:100%;height:100%;background:linear-gradient(160deg,#6f6e6b,#3b3a38)"></div></div>
  <div class="thumb" style="left:457px" role="img" aria-label="Silver convertible under workshop lights"><div style="width:100%;height:100%;background:linear-gradient(160deg,#bdbab4,#5a5854)"></div></div>
  <div class="thumb" style="left:761px" role="img" aria-label="Car interior with cream leather seats"><div style="width:100%;height:100%;background:linear-gradient(160deg,#8e8780,#2e2b29)"></div></div>
  <div class="arrow" style="left:1106px"><svg viewBox="0 0 20 28"><path d="M5 3l10 11L5 25"/></svg></div>
</section>

<section class="partners">
  <span>GLENBRUSH</span><span>VASTINCO</span><span>KEBO</span><span>Q WRAP</span><span>DORFLINT</span>
</section>

<section class="contact">
  <div class="map" role="img" aria-label="Street map around the bodyshop location"></div>
  <div class="contact-panel">
    <h2>CONTACT <b>US</b></h2>
    <div class="input" style="left:44px;top:86px;width:224px">First Name</div>
    <div class="input" style="left:284px;top:86px;width:224px">Last Name</div>
    <div class="input" style="left:44px;top:144px;width:224px">Email</div>
    <div class="input" style="left:284px;top:144px;width:224px">Phone</div>
    <div class="input" style="left:44px;top:202px;width:464px;height:124px">Message</div>
    <span class="btn">Send</span>
    <div class="info" style="left:44px;top:428px;width:200px"><svg viewBox="0 0 16 16"><path d="M8 0a5 5 0 0 0-5 5c0 4 5 11 5 11s5-7 5-11a5 5 0 0 0-5-5z"/></svg><div>Fernlow Business Park,<br>Kiln Lane, Ashcombe,<br>Derbyshire,<br>DE99 2QX</div></div>
    <div class="info" style="left:284px;top:428px"><svg viewBox="0 0 24 24"><path d="M6.6 10.8a15 15 0 0 0 6.6 6.6l2.2-2.2c.3-.3.7-.4 1-.2 1.1.4 2.3.6 3.6.6.6 0 1 .4 1 1V20c0 .6-.4 1-1 1A17 17 0 0 1 3 4c0-.6.4-1 1-1h3.5c.6 0 1 .4 1 1 0 1.3.2 2.5.6 3.6.1.3 0 .7-.2 1z"/></svg>07700 900418</div>
    <div class="info" style="left:284px;top:458px"><svg viewBox="0 0 24 24"><path d="M2 5h20v14H2z"/></svg>sales@brenvashine.co.uk</div>
  </div>
</section>

<footer class="site-footer">
  <div class="brand-f"><div class="name">BRENVASHINE</div><div class="sub">BODYSHOP</div></div>
  <div class="foot-nav"><span>Home</span>|<span>About Us</span>|<span>Service</span>|<span>Custom</span>|<span>Gallery</span>|<span>Contact</span></div>
  <div class="foot-services"><span>Full or part resprays</span>|<span>Dents &amp; scratch removal</span>|<span>Bumper repair</span>|<span>Accident repair</span>|<span>Alloy wheel's refurbished, repaired &amp; painted</span></div>
  <div class="pay">TILLWAVE</div>
  <div class="copy">Copyrights © 2019.The Company Name. All rights reserved.</div>
  <div class="code-tag">C28</div>
</footer>

</body>
</html>
```